Business Card Design

We need a business card designed for our new company. Prefer a black card with white logo & writing.

Contact Information for Business Card

Ted Galloway, address: 7-4812 Fernhollow Road, Abbotsford, BC, V3K 8R2, Office Phone: 604-712-3390, Cell: 604-947-2164, Email: ted@resinworkshub.ca

Colors

Designer to choose only greyscale colors for use in the design.

```html
<!DOCTYPE html>
<html lang="en">
<head>
<meta charset="utf-8">
<title>Resinworks Hub — Business Card</title>
<link rel="stylesheet" href="https://fonts.googleapis.com/css2?family=Montserrat:wght@300;400;700&display=swap">
<style>
  :root {
    --backdrop: #262626;
    --card: #000000;
    --ink: #ffffff;
  }
  * { margin: 0; padding: 0; box-sizing: border-box; }
  html, body {
    width: 1200px;
    height: 900px;
    overflow: hidden;
    background: var(--backdrop);
  }
  .canvas {
    position: relative;
    width: 1200px;
    height: 900px;
  }
  .card {
    position: absolute;
    left: 341px;
    width: 518px;
    height: 296px;
    background: var(--card);
    color: var(--ink);
    font-family: "Montserrat", sans-serif;
  }
  .card--front { top: 141px; }
  .card--back {
    top: 463px;
    display: flex;
    align-items: center;
    justify-content: center;
  }
  .holder-name {
    position: absolute;
    top: 86px;
    width: 100%;
    text-align: center;
    font-size: 29px;
    font-weight: 300;
    letter-spacing: 2px;
    text-transform: uppercase;
  }
  .divider {
    position: absolute;
    top: 133px;
    left: 238px;
    width: 42px;
    height: 1px;
    background: var(--ink);
  }
  .contact {
    position: absolute;
    top: 148px;
    width: 100%;
    text-align: center;
    font-size: 12.5px;
    font-weight: 400;
    line-height: 18px;
  }
  .contact .gap { display: inline-block; width: 14px; }
  .brand {
    display: flex;
    align-items: center;
    gap: 14px;
  }
  .brand-dot {
    width: 22px;
    height: 22px;
    border-radius: 50%;
    background: var(--ink);
  }
  .brand-name {
    font-size: 34px;
    font-weight: 700;
    letter-spacing: 1px;
    text-transform: uppercase;
    color: var(--ink);
  }
</style>
</head>
<body>
  <main class="canvas">
    <section class="card card--front">
      <h1 class="holder-name">Ted Galloway</h1>
      <div class="divider"></div>
      <p class="contact">
        Phone 604-712-3390<span class="gap"></span>Cell Phone 604-947-2164<br>
        E ted@resinworkshub.ca<span class="gap"></span>W&nbsp; resinworkshub.ca<br>
        7-4812 Fernhollow Road, Abbotsford, BC, V3K 8R2
      </p>
    </section>
    <section class="card card--back">
      <div class="brand">
        <span class="brand-dot"></span>
        <span class="brand-name">Resinworks Hub</span>
      </div>
    </section>
  </main>
</body>
</html>
```